A clean crisp business card for a Landscape Construction company. Designed to be easy to read contact/ info and also be appealing/interesting, unlike a traditional business card.

Industry/Entity Type

Landscape Construction

Contact Information for Business Card

Company name : Brambleford Landscape Construction, phone number: (877) 62Vista, website:Bramblefordyards.example, Email, sales@bramblefordyards.example

Requirements
Nice to have
• Luxurious finishes/ details…. Icons or emblems next to contact info
Should not have
• Clipart or general pictures

```html
<!DOCTYPE html>
<html lang="en">
<head>
<meta charset="utf-8">
<title>Brambleford Landscape Construction – Business Card</title>
<link rel="stylesheet" href="https://fonts.googleapis.com/css2?family=Cinzel:wght@400;600&family=Open+Sans:wght@400;600&display=swap">
<style>
  :root {
    --stage: #ece9e4;
    --leaf: #8cc63f;
    --leaf-light: #a3d45e;
    --sky: #3f7fd0;
    --ink: #121212;
    --ink-soft: #2a2a2a;
    --paper: #ffffff;
    --muted: #e6e6e6;
  }
  * { margin: 0; padding: 0; box-sizing: border-box; }
  html, body { width: 1200px; height: 913px; overflow: hidden; }
  body {
    background: var(--stage);
    display: flex;
    align-items: center;
    justify-content: center;
    gap: 48px;
    font-family: "Open Sans", Arial, sans-serif;
  }
  .card {
    width: 540px;
    height: 309px;
    border-radius: 4px;
    position: relative;
    overflow: hidden;
    box-shadow: 0 10px 28px rgba(0,0,0,.18);
  }

  /* Front */
  .card--front {
    background: linear-gradient(135deg, var(--leaf-light), var(--leaf) 55%);
    display: flex;
    flex-direction: column;
    align-items: center;
    justify-content: center;
    color: var(--paper);
  }
  .wordmark {
    display: flex;
    align-items: center;
    gap: 14px;
    font-family: "Cinzel", Georgia, serif;
    font-weight: 400;
  }
  .wordmark__dot {
    width: 34px; height: 34px;
    border-radius: 50%;
    flex: none;
  }
  .wordmark__name { line-height: 1.15; }
  .card--front .wordmark__dot { background: var(--sky); }
  .card--front .wordmark__name { font-size: 30px; color: var(--paper); }
  .card--front .wordmark__name span { display: block; font-size: 15px; letter-spacing: 3px; }
  .front-url {
    margin-top: 34px;
    font-family: "Cinzel", Georgia, serif;
    font-size: 13px;
    letter-spacing: 2px;
  }

  /* Back */
  .card--back {
    background: linear-gradient(125deg, var(--ink) 40%, var(--ink-soft) 75%, var(--ink) 100%);
    display: flex;
    align-items: center;
    padding: 0 30px;
    color: var(--paper);
  }
  .card--back .wordmark { width: 215px; gap: 10px; }
  .card--back .wordmark__dot { width: 24px; height: 24px; background: var(--sky); }
  .card--back .wordmark__name { font-size: 19px; color: var(--leaf); }
  .card--back .wordmark__name span { display: block; font-size: 10px; letter-spacing: 1.5px; }
  .divider { width: 8px; height: 170px; margin: 0 22px 0 10px; flex: none; }
  .contact { font-size: 11.5px; line-height: 1.65; }
  .contact__name {
    font-family: "Cinzel", Georgia, serif;
    font-size: 19px;
    letter-spacing: 1px;
    line-height: 1.2;
  }
  .contact__first { color: var(--sky); }
  .contact__last { color: var(--leaf); }
  .contact__role { margin-bottom: 8px; }
  .contact__row { display: flex; align-items: center; gap: 7px; }
  .contact__row svg { width: 12px; height: 12px; flex: none; }
</style>
</head>
<body>

  <section class="card card--front">
    <div class="wordmark">
      <div class="wordmark__dot"></div>
      <div class="wordmark__name">Brambleford<span>Landscape Construction</span></div>
    </div>
    <p class="front-url">WWW.BRAMBLEFORDYARDS.EXAMPLE</p>
  </section>

  <section class="card card--back">
    <div class="wordmark">
      <div class="wordmark__dot"></div>
      <div class="wordmark__name">Brambleford<span>Landscape Construction</span></div>
    </div>

    <svg class="divider" viewBox="0 0 8 170" aria-hidden="true">
      <line x1="1" y1="0" x2="1" y2="170" stroke="var(--leaf)" stroke-width="1.2"/>
      <line x1="5" y1="20" x2="5" y2="150" stroke="var(--sky)" stroke-width="2.5"/>
    </svg>

    <div class="contact">
      <p class="contact__name"><span class="contact__first">Elena</span> <span class="contact__last">Marsh</span></p>
      <p class="contact__role">Director</p>
      <p>4710 Fairhollow Rd.,</p>
      <p>Suite 112, Cedar Vale, OH 45000</p>
      <p class="contact__row">
        <svg viewBox="0 0 12 12" aria-hidden="true"><path d="M2.5 1 L4.5 1 L5.2 3.5 L4 4.6 Q5 7 7.4 8 L8.5 6.8 L11 7.5 L11 9.5 Q10.5 11 9 11 Q1 10 1 3 Q1 1.5 2.5 1 Z" fill="var(--leaf)"/></svg>
        (877) 62Vista
      </p>
      <p class="contact__row">
        <svg viewBox="0 0 12 12" aria-hidden="true"><rect x="0.5" y="2.5" width="11" height="7.5" fill="var(--leaf)"/><path d="M0.5 2.5 L6 7 L11.5 2.5" fill="none" stroke="var(--ink)" stroke-width="1"/></svg>
        sales@bramblefordyards.example
      </p>
      <p class="contact__row">
        <svg viewBox="0 0 12 12" aria-hidden="true"><circle cx="6" cy="6" r="5.5" fill="var(--leaf)"/><path d="M0.5 6 H11.5 M6 0.5 Q3 6 6 11.5 M6 0.5 Q9 6 6 11.5" fill="none" stroke="var(--ink)" stroke-width="0.8"/></svg>
        www.bramblefordyards.example
      </p>
    </div>
  </section>

</body>
</html>
```